Upscale business cards needed for Board of Directors

We need professional business cards created for members of our family business Board of Directors. We would like these relatively simple and straightforward, but also with a unique element to set them apart. Probably stick with neutral and simple colors - white, grey etc. We need space for the traditional elements, including name, title, address, email/phone number. And we will be creating several from this template so it needs to be template that is easy to switch information in and out of.
Business
See description

```html
<!DOCTYPE html>
<html lang="en">
<head>
<meta charset="utf-8">
<title>Harborline Holdings – Business Card</title>
<link rel="stylesheet" href="https://fonts.googleapis.com/css2?family=Lato:wght@400;700;900&display=swap">
<style>
  :root {
    --gold: #b19d70;
    --ink: #111111;
    --paper: #ffffff;
    --stage: #3a3a3a;
  }
  * { margin: 0; padding: 0; box-sizing: border-box; }
  html, body { width: 1200px; height: 900px; overflow: hidden; }
  body {
    background: var(--stage);
    font-family: 'Lato', Arial, sans-serif;
    position: relative;
  }
  .card {
    position: absolute;
    width: 560px;
    height: 322px;
    overflow: hidden;
  }

  /* Back of card */
  .card-back {
    left: 570px; top: 70px;
    background: var(--gold);
    color: var(--paper);
    display: flex;
    flex-direction: column;
    align-items: center;
    justify-content: center;
  }
  .card-back .brand-name {
    font-weight: 900;
    font-size: 44px;
    letter-spacing: 1px;
    line-height: 1;
    text-align: center;
  }
  .card-back .brand-sub {
    font-weight: 900;
    font-size: 24px;
    letter-spacing: 12px;
    margin-top: 8px;
    padding-left: 12px;
  }
  .card-back .web {
    margin-top: 38px;
    font-size: 15px;
    letter-spacing: 2px;
  }

  /* Front of card */
  .card-front {
    left: 70px; top: 470px;
    width: 600px; height: 345px;
    background: var(--paper);
    color: var(--ink);
  }
  .card-front .brand {
    position: absolute;
    left: 44px; top: 30px;
    font-weight: 900;
    color: var(--ink);
  }
  .card-front .brand-name { font-size: 40px; line-height: 1; letter-spacing: 1px; }
  .card-front .brand-sub {
    font-size: 21px; letter-spacing: 11px; margin-top: 6px; padding-left: 30px;
  }
  .contact-list {
    position: absolute;
    left: 44px; top: 126px;
    list-style: none;
    font-size: 16px;
    line-height: 21px;
  }
  .contact-list li { display: flex; align-items: center; gap: 10px; }
  .contact-list svg { width: 13px; height: 13px; fill: var(--gold); flex: none; }
  .person {
    position: absolute;
    right: 40px; top: 176px;
    text-align: right;
  }
  .person .name { color: var(--gold); font-size: 26px; line-height: 1.1; }
  .person .title { font-size: 18px; margin-bottom: 16px; }
  .person .address { font-size: 18px; line-height: 22px; }
  .swoosh { position: absolute; left: 0; top: 0; width: 600px; height: 345px; }
</style>
</head>
<body>

<section class="card card-back">
  <div class="brand-name">HARBORLINE</div>
  <div class="brand-sub">HOLDINGS</div>
  <div class="web">www.harborline.com</div>
</section>

<section class="card card-front">
  <svg class="swoosh" viewBox="0 0 600 345" aria-hidden="true">
    <path d="M0,214 C170,240 360,300 540,345 L470,345 C330,318 160,270 0,252 Z" fill="var(--ink)"/>
    <path d="M0,258 C190,296 420,346 600,306 L600,345 L0,345 Z" fill="var(--gold)"/>
  </svg>

  <div class="brand">
    <div class="brand-name">HARBORLINE</div>
    <div class="brand-sub">HOLDINGS</div>
  </div>

  <ul class="contact-list">
    <li><svg viewBox="0 0 16 16"><path d="M3 1l3 0 1 4-2 1c1 2 3 4 5 5l1-2 4 1 0 3c0 1-1 2-2 2C7 15 1 9 1 3c0-1 1-2 2-2z"/></svg>512 555 0140</li>
    <li><svg viewBox="0 0 16 16"><path d="M4 1h8v4H4zM1 6h14v6h-3v3H4v-3H1zM5 10v4h6v-4z"/></svg>512 555 0141</li>
    <li><svg viewBox="0 0 16 16"><path d="M1 3h14v10H1zM2 4l6 5 6-5v-0.5H2z"/></svg>info@harborline.com</li>
    <li><svg viewBox="0 0 16 16"><circle cx="8" cy="8" r="7"/></svg>www.harborline.com</li>
  </ul>

  <div class="person">
    <div class="name">Daniel Whitmore</div>
    <div class="title">Director</div>
    <div class="address">1450 Cedar Lane<br>Millbrook TX 78010</div>
  </div>
</section>

</body>
</html>
```